Commercial Rooftop Solar business needs a website

We need a website with fantastic appeal for a new company based in Melbourne called Tallow Ridge Energy. We design and install solar energy systems for commercial applications across Australia. Our market is to focus on small to medium businesses looking for solar solutions, but we will also provide our service for residential customers. We would like a beautiful 'front page' feel to our home page, using photographs of solar PV systems and/or natural imagery. Our logo uses the colours orange and black, which could easily be echoed in photographic imagery of sunset and sunrise, for example. The design should communicate quiet confidence and professionalism to a corporate marketplace.

NEW POINTS FOR BRIEF: This design also needs to be flexible to allow for additional future content, including a Support page with sub pages, FAQ's, and a Blog.

As part of this design project, we will require the coding for the website to be completed by the designer.

We have seen some websites, which we like the look and feel of: these are listed below.

brightvanepower.com.au:

• Beautiful images underlaying brief text selling points.
• Simple ‘front cover’ style home page with elegant drop-down menu, stylish simple font style.
• Home page invites exploration through the menu links, rather than trying to provide all the information up front.
• Company logo and name in the top left hand corner, contact details accessible at top right hand, seems consistent in most sites.

kelpworks.com.au

rumbofield.com:
• Same element as the others is the front-page style home page with beautiful images underlying text.

We have a webpage that we started uploading content to. You can use some of the content there in your designs: www.tallowridgeenergy.com.au

Technical Specifications:
PAGES:

Home

About Us

Solutions - Commercial
- Residential

Products - Solar Panels - Vorla Heron, Vorla TELD, Vorla QB
- Solar Inverters - Kestamo, BrilQuill
- Monitoring systems - Dunmere Metrics
- Batteries - RW

- Datasheets have been provided for reference but if it's too much work, you can use generic text and we will provide content later.

Contact Us

FUTURE PAGES (Please consider in structure, where links could be placed):

Support

FAQ's

Blog.

We could provide some content for the Support page soon, but the Blog and FAQ's are future pages which we don't want highlighted in the design as we don't yet have content.

Phone: 1800 7 BIRCH
Email: sales@tallowridgeenergy.com.au

Currently, I do not have images and text available. Please
use placeholders in the meantime. The final text and images will be uploaded for the winner once a winning design has been selected.

Target Market(s)

Primary focus is on small to medium sized business owners. Those owners will have a house which may be suitable for solar so we want to cater to residential deeper in the website.

Industry/Entity Type

Solar Energy

Coding

Coded - Design and coding required

Number of Pages Required

5+ page

Colors
f78f20
0255a3

Requirements
Must have
• Logo as per attachments.
Nice to have
• Logo can have alternate colours Eg. White on Orange or Black etc. provided colour correct logo is shown somewhere eg. footer or contact page.
• In the active site, I'd like to have:
• Very slowly zooming images - barely perceptible.
• Title text that rolls into place
• Subtle movements
• See https://plumtally.com.au/ for example

```html
<!DOCTYPE html>
<html lang="en">
<head>
<meta charset="utf-8">
<title>Tallow Ridge Energy</title>
<link href="https://fonts.googleapis.com/css2?family=Open+Sans:wght@400;600;700&family=Roboto:wght@400;500;700&display=swap" rel="stylesheet">
<style>
:root{
  --orange:#ee5a24;
  --orange-dark:#d94c1a;
  --ink:#333333;
  --text:#555555;
  --grey:#777777;
  --grey-btn:#7a7a7a;
  --dark-panel:#4a4a4a;
  --footer:#565656;
  --footer-line:#7a7a7a;
  --white:#ffffff;
}
*{box-sizing:border-box;margin:0;padding:0}
html,body{width:1200px;height:2817px;overflow:hidden}
body{font-family:"Open Sans",Arial,sans-serif;color:var(--text);background:var(--white);position:relative}
a{color:inherit;text-decoration:none}
.abs{position:absolute}

/* Header */
.topline{position:absolute;left:0;top:0;width:1200px;height:4px;background:var(--orange)}
.site-header{position:absolute;left:0;top:4px;width:1200px;height:127px;background:var(--white)}
.brand{position:absolute;left:98px;top:34px;display:flex;align-items:center;gap:12px;font-family:"Roboto",Arial,sans-serif;font-weight:700;font-size:25px;color:var(--orange)}
.brand-dot{width:30px;height:30px;border-radius:50%;background:#2b2b2b}
.contact-bar{position:absolute;top:20px;right:98px;display:flex;gap:30px;align-items:center;font-size:17px;color:var(--grey)}
.contact-item{display:flex;align-items:center;gap:10px}
.contact-item .ic{width:34px;height:34px;border-radius:50%;display:flex;align-items:center;justify-content:center}
.contact-item.mail .ic{background:#8a8a8a}
.contact-item.phone .ic{background:var(--orange)}
.contact-item.phone{color:var(--orange);font-weight:700;font-size:18px}
.main-nav{position:absolute;top:72px;right:98px;display:flex;align-items:center;gap:0;font-family:"Roboto",Arial,sans-serif;font-weight:500;font-size:15px;color:#333}
.main-nav a{padding:8px 22px;margin-left:38px;border-radius:16px}
.main-nav a.active{background:var(--orange);color:var(--white);margin-left:0}

/* Hero */
.hero{position:absolute;left:0;top:131px;width:1200px;height:513px}
.hero-photo{position:absolute;inset:0;background:linear-gradient(100deg,#1d3f7a 0%,#3c6fb8 32%,#6ea3d8 52%,#9cc4e6 66%,#b9d5a0 82%,#6f9f3c 100%)}
.hero-copy{position:absolute;left:714px;top:104px;width:440px;color:var(--white)}
.hero-copy h1{font-family:"Roboto",Arial,sans-serif;font-weight:500;font-size:52px;letter-spacing:1px;line-height:1}
.hero-copy p{font-size:14px;font-weight:600;line-height:22px;margin-top:30px}
.btn-outline{display:inline-block;margin-top:22px;background:var(--orange);color:var(--white);border:2px solid var(--white);font-size:13px;font-weight:600;padding:10px 16px}
.slide-arrow{position:absolute;top:240px;width:32px;height:32px;border-radius:50%;background:rgba(0,0,0,.35);display:flex;align-items:center;justify-content:center}

/* Feature boxes */
.features{position:absolute;left:98px;top:550px;width:1002px;height:186px;display:flex;box-shadow:0 26px 30px -18px rgba(0,0,0,.35)}
.feature{flex:1;display:flex;gap:24px;padding:42px 26px 0 22px;color:var(--white)}
.feature.commercial{background:var(--orange)}
.feature.residential{background:var(--dark-panel)}
.feature h3{font-family:"Roboto",Arial,sans-serif;font-weight:500;font-size:19px;margin-bottom:12px}
.feature p{font-size:12.5px;line-height:20px}
.feature .fic{flex:0 0 74px;height:74px;display:flex;align-items:center;justify-content:center}

/* Welcome */
.section-title{position:absolute;left:0;width:1200px;text-align:center;font-family:"Roboto",Arial,sans-serif;font-weight:500;font-size:32px;color:var(--orange)}
.section-lead{position:absolute;left:170px;width:860px;text-align:center;font-size:14px;line-height:23px;color:var(--grey)}
.services{position:absolute;left:0;top:975px;width:1200px}
.service{position:absolute;width:300px;text-align:center}
.service .drop{width:162px;height:162px;margin:0 auto;border-radius:50% 0 50% 50%;background:var(--grey-btn);display:flex;align-items:center;justify-content:center}
.service.highlight .drop{background:var(--orange)}
.service h3{font-family:"Roboto",Arial,sans-serif;font-weight:400;font-size:21px;color:var(--grey);margin-top:36px}
.service.highlight h3{color:var(--orange);font-weight:500}
.service p{font-size:13px;line-height:23px;color:#444;margin-top:14px}
.btn{display:inline-block;font-family:"Roboto",Arial,sans-serif;font-size:14px;font-weight:500;color:var(--white);background:var(--grey-btn);padding:14px 0;width:128px;margin-top:30px;border-radius:3px}
.service.highlight .btn{background:var(--orange)}

/* Systems band */
.systems-band{position:absolute;left:0;top:1431px;width:1200px;height:485px;background:linear-gradient(180deg,#b48a55 0%,#d9a45a 28%,#9a7a55 52%,#4c5660 70%,#55602f 88%,#3f4a1f 100%)}
.systems-panel{position:absolute;left:98px;top:58px;width:668px;height:333px;background:rgba(60,60,60,.72);padding:28px 24px;color:var(--white)}
.systems-panel h2{font-family:"Roboto",Arial,sans-serif;font-weight:500;font-size:27px}
.systems-panel p{font-size:13px;line-height:22px;margin-top:18px;color:#eeeeee}
.systems-panel ul{list-style:none;margin-top:20px}
.systems-panel li{font-size:13px;font-weight:600;display:flex;align-items:center;gap:14px;height:31px}
.systems-panel li::before{content:"";width:10px;height:10px;border-radius:50%;border:3px solid var(--white)}

/* Blog */
.post{position:absolute;top:2137px;width:490px;height:196px}
.post .thumb{position:absolute;left:0;top:0;width:242px;height:196px}
.post .body{position:absolute;left:264px;top:0;width:226px}
.post h4{font-family:"Roboto",Arial,sans-serif;font-weight:500;font-size:17px;color:#222}
.post p{font-size:11.5px;line-height:21.5px;color:#444;margin-top:12px;text-align:justify}
.btn-pill{display:inline-block;background:var(--orange);color:var(--white);font-size:11px;padding:10px 28px;border-radius:20px;margin-top:18px}

/* Footer */
.site-footer{position:absolute;left:0;top:2411px;width:1200px;height:406px;background:var(--footer);color:var(--white)}
.footer-brand{position:absolute;left:98px;top:120px;width:200px;text-align:center}
.footer-brand .mark{width:110px;height:110px;border-radius:50%;background:rgba(255,255,255,.9);margin:0 auto 18px}
.footer-brand .name{font-family:"Roboto",Arial,sans-serif;font-weight:500;font-size:22px;color:var(--white)}
.fcol{position:absolute;top:50px}
.fcol h5{font-family:"Roboto",Arial,sans-serif;font-weight:500;font-size:17px;letter-spacing:.5px}
.fcol h5::after{content:"";display:block;width:110px;height:1px;background:#bbbbbb;margin-top:10px}
.finfo{display:flex;gap:18px;margin-top:22px}
.finfo .ring{flex:0 0 38px;height:38px;border:2px solid var(--white);border-radius:50%;display:flex;align-items:center;justify-content:center}
.finfo b{display:block;font-size:14px;font-weight:600}
.finfo span{display:block;font-size:12px;line-height:20px;color:#e4e4e4;margin-top:4px}
.links{list-style:none;margin-top:14px}
.links li{font-size:13px;height:28px;display:flex;align-items:center;gap:12px}
.links li.sub{padding-left:34px}
.links li:not(.sub)::before{content:"";width:8px;height:8px;border-radius:50%;border:3px solid var(--white)}
.cform{margin-top:26px;width:254px}
.cform .row{display:flex;gap:8px}
.field{border:1px solid #cfcfcf;border-radius:3px;font-size:10px;padding:10px 9px;color:#eeeeee;height:38px;flex:1}
.field.area{height:66px;margin-top:10px}
.btn-send{display:inline-block;background:var(--white);color:var(--orange);font-size:11px;font-weight:600;padding:11px 12px;margin-top:14px;border-radius:2px}
.footer-rule{position:absolute;left:98px;top:331px;width:1002px;height:1px;background:var(--footer-line)}
.copyright{position:absolute;left:98px;top:360px;font-size:13px;color:#eeeeee}
.social{position:absolute;right:100px;top:350px;display:flex;gap:8px}
.social span{width:34px;height:34px;border:2px solid var(--white);border-radius:50%;display:block}
</style>
</head>
<body>

<div class="topline"></div>
<header class="site-header">
  <a class="brand" href="#"><span class="brand-dot"></span>Tallow Ridge Energy</a>
  <div class="contact-bar">
    <div class="contact-item mail"><span class="ic"><svg width="16" height="12" viewBox="0 0 16 12"><rect x="1" y="1" width="14" height="10" fill="none" stroke="#fff" stroke-width="1.6"/><path d="M1 1l7 6 7-6" fill="none" stroke="#fff" stroke-width="1.6"/></svg></span>info@tallowridgeenergy.com</div>
    <div class="contact-item phone"><span class="ic"><svg width="16" height="16" viewBox="0 0 24 24"><path d="M6.6 10.8a15 15 0 006.6 6.6l2.2-2.2c.3-.3.7-.4 1-.2 1.1.4 2.3.6 3.6.6.6 0 1 .4 1 1V20c0 .6-.4 1-1 1A17 17 0 013 4c0-.6.4-1 1-1h3.5c.6 0 1 .4 1 1 0 1.3.2 2.5.6 3.6.1.3 0 .7-.2 1z" fill="#fff"/></svg></span>180 041 7729</div>
  </div>
  <nav class="main-nav">
    <a class="active" href="#">HOME</a>
    <a href="#">ABOUT US</a>
    <a href="#">SOLUTIONS</a>
    <a href="#">CONTACT US</a>
  </nav>
</header>

<section class="hero">
  <div class="hero-photo" role="img" aria-label="Photo of rooftop solar panels under a bright blue sky beside green grass"></div>
  <div class="hero-copy">
    <h1>TALLOW RIDGE ENERGY</h1>
    <p>We design and install solar energy systems for commercial applications across Australia.</p>
    <a class="btn-outline" href="#">READ MORE</a>
  </div>
  <span class="slide-arrow" style="left:34px"><svg width="12" height="12" viewBox="0 0 12 12"><path d="M8 1L3 6l5 5" fill="none" stroke="#fff" stroke-width="2"/></svg></span>
  <span class="slide-arrow" style="right:34px"><svg width="12" height="12" viewBox="0 0 12 12"><path d="M4 1l5 5-5 5" fill="none" stroke="#fff" stroke-width="2"/></svg></span>
</section>

<div class="features">
  <div class="feature commercial">
    <div class="fic"><svg width="68" height="54" viewBox="0 0 68 54"><path d="M12 4h52l-8 34H4z" fill="none" stroke="#fff" stroke-width="2.5"/><path d="M30 4l-6 34M47 4l-7 34M8 21h52" stroke="#fff" stroke-width="2"/><path d="M30 38v10M20 50h22" stroke="#fff" stroke-width="2.5"/></svg></div>
    <div><h3>COMMERCIAL</h3><p>We design and install solar energy systems for commercial applications across Australia. Nemo enim ipsam voluptatem quia voluptas sit aspernatur aut odit aut fugit.</p></div>
  </div>
  <div class="feature residential">
    <div class="fic"><svg width="66" height="66" viewBox="0 0 66 66"><circle cx="33" cy="33" r="30" fill="none" stroke="#fff" stroke-width="2" stroke-dasharray="3 4"/><path d="M33 12c8 12 14 19 14 27a14 14 0 01-28 0c0-8 6-15 14-27z" fill="#fff"/><path d="M35 28l-7 11h6l-3 9 8-12h-6z" fill="#4a4a4a"/></svg></div>
    <div><h3>RESIDENTIAL</h3><p>We design and install solar energy systems for commercial applications across Australia. Nemo enim ipsam voluptatem quia voluptas sit aspernatur aut odit aut fugit.</p></div>
  </div>
</div>

<h2 class="section-title" style="top:812px">Welcome To Tallow Ridge Energy</h2>
<p class="section-lead" style="top:872px">We design and install solar energy systems for commercial applications across Australia. Nemo enim ipsam voluptatem quia voluptas sit aspernatur aut odit aut fugit.</p>

<section class="services">
  <div class="service" style="left:90px">
    <div class="drop"><svg width="84" height="84" viewBox="0 0 84 84"><g stroke="#fff" stroke-width="3" fill="none"><circle cx="42" cy="42" r="17"/><path d="M42 6v12M42 66v12M6 42h12M66 42h12M17 17l8 8M59 59l8 8M17 67l8-8M59 25l8-8"/></g><path d="M45 30l-10 14h7l-4 11 11-15h-7z" fill="#fff"/></svg></div>
    <h3>Solar PV Systems</h3>
    <p>Nemo enim ipsam voluptatem quia voluptas sit aspernatur aut odit aut fugit, sed quia con sequuntur magni dolores.</p>
    <a class="btn" href="#">READ MORE</a>
  </div>
  <div class="service highlight" style="left:449px">
    <div class="drop"><svg width="80" height="80" viewBox="0 0 80 80"><g fill="#fff"><rect x="14" y="12" width="14" height="10"/><rect x="33" y="12" width="14" height="10"/><rect x="52" y="12" width="14" height="10"/><rect x="14" y="26" width="14" height="10"/><rect x="33" y="26" width="14" height="10"/><rect x="52" y="26" width="14" height="10"/><rect x="14" y="40" width="14" height="10"/><rect x="33" y="40" width="14" height="10"/><rect x="52" y="40" width="14" height="10"/><rect x="37" y="54" width="6" height="12"/><rect x="26" y="66" width="28" height="4"/></g></svg></div>
    <h3>Solar Energy Systems</h3>
    <p>Nemo enim ipsam voluptatem quia voluptas sit aspernatur aut odit aut fugit, sed quia con sequuntur magni dolores.</p>
    <a class="btn" href="#">READ MORE</a>
  </div>
  <div class="service" style="left:810px">
    <div class="drop"><svg width="84" height="84" viewBox="0 0 84 84"><g stroke="#fff" stroke-width="3" fill="none"><path d="M42 6v8M14 18l6 6M70 18l-6 6M6 42h8M70 42h8"/></g><circle cx="42" cy="42" r="18" fill="#fff"/><rect x="34" y="58" width="16" height="8" fill="#fff"/><path d="M36 34v8M48 34v8M34 42h16v4a8 8 0 01-16 0z" stroke="#777" stroke-width="3" fill="none"/></svg></div>
    <h3>Tallow Ridge Energy</h3>
    <p>Nemo enim ipsam voluptatem quia voluptas sit aspernatur aut odit aut fugit, sed quia con sequuntur magni dolores.</p>
    <a class="btn" href="#">READ MORE</a>
  </div>
</section>

<section class="systems-band" role="img" aria-label="Photo of a solar farm and wind turbines at sunset with a city skyline">
  <div class="systems-panel">
    <h2>Solar Energy Systems</h2>
    <p>Nemo enim ipsam voluptatem quia voluptas sit aspernatur aut odit aut fugit, sed quia consequ untur magni dolores eos qui ratione voluptatem sequi nesciunt.</p>
    <ul>
      <li>Solar PV systems</li>
      <li>Commercial</li>
      <li>Residential</li>
      <li>Tallow Ridge Energy</li>
      <li>Solar energy systems</li>
    </ul>
  </div>
</section>

<h2 class="section-title" style="top:1972px">Our Blog Posts</h2>
<p class="section-lead" style="top:2028px">Nemo enim ipsam voluptatem quia voluptas sit aspernatur aut odit aut fugit, sed quia consequuntur magni dolores eos qui ratione voluptatem sequi nesciunt.</p>

<article class="post" style="left:98px">
  <div class="thumb" role="img" aria-label="Photo of suburban red-tiled roofs with solar panels" style="background:linear-gradient(180deg,#9cc7e2 0%,#c9d9e0 40%,#a0533a 62%,#3e5a8c 80%,#6a7a3e 100%)"></div>
  <div class="body">
    <h4>SOLAR ENERGY SYSTEMS</h4>
    <p>Nemo enim ipsam voluptatem quia voluptas sit aspernatur aut odit aut fugit, sed quia consequuntur magni dolores eos qui ratione voluptatem sequi nesciunt.</p>
    <a class="btn-pill" href="#">CLICK HERE</a>
  </div>
</article>
<article class="post" style="left:614px">
  <div class="thumb" role="img" aria-label="Photo of an installer fitting solar panels on a roof" style="background:linear-gradient(150deg,#7fa7c9 0%,#2f5e9e 40%,#1d3f78 70%,#4a6a9a 100%)"></div>
  <div class="body">
    <h4>TALLOW RIDGE ENERGY</h4>
    <p>Nemo enim ipsam voluptatem quia voluptas sit aspernatur aut odit aut fugit, sed quia consequuntur magni dolores eos qui ratione voluptatem sequi nesciunt.</p>
    <a class="btn-pill" href="#">CLICK HERE</a>
  </div>
</article>

<footer class="site-footer">
  <div class="footer-brand"><div class="mark"></div><div class="name">Tallow Ridge Energy</div></div>

  <div class="fcol" style="left:375px">
    <h5>CONTACT US</h5>
    <div class="finfo"><span class="ring"><svg width="14" height="18" viewBox="0 0 14 18"><path d="M7 1a6 6 0 016 6c0 4-6 10-6 10S1 11 1 7a6 6 0 016-6z" fill="none" stroke="#fff" stroke-width="1.8"/><circle cx="7" cy="7" r="2" fill="#fff"/></svg></span><div><b>ADDRESS,</b><span>77 Quarry Lane, Brunswick<br>3056, AUS</span></div></div>
    <div class="finfo"><span class="ring"><svg width="12" height="18" viewBox="0 0 12 18"><rect x="1.5" y="1" width="9" height="16" rx="1.5" fill="none" stroke="#fff" stroke-width="1.8"/><circle cx="6" cy="14" r="1" fill="#fff"/></svg></span><div><b>PHONE:</b><span>180 041 7729</span></div></div>
    <div class="finfo"><span class="ring"><svg width="16" height="12" viewBox="0 0 16 12"><rect x="1" y="1" width="14" height="10" fill="#fff"/><path d="M1 1l7 6 7-6" fill="none" stroke="#565656" stroke-width="1.4"/></svg></span><div><b>Mail:</b><span>info@tallowridgeenergy.com</span></div></div>
  </div>

  <div class="fcol" style="left:628px">
    <h5>QUICK LINKS</h5>
    <ul class="links">
      <li>Home</li>
      <li>About Us</li>
      <li>Solutions</li>
      <li class="sub">Commercial</li>
      <li class="sub">Residential</li>
      <li>Contact us</li>
    </ul>
  </div>

  <div class="fcol" style="left:847px">
    <h5>CONTACT FORM</h5>
    <div class="cform">
      <div class="row"><div class="field">Name</div><div class="field">Phone</div></div>
      <div class="field area">Address</div>
      <a class="btn-send" href="#">SEND MESSAGE</a>
    </div>
  </div>

  <div class="footer-rule"></div>
  <p class="copyright">Copyright © 2017 Tallow Ridge Energy. All Right Reserved</p>
  <div class="social"><span></span><span></span><span></span><span></span></div>
</footer>

</body>
</html>
```